Coaching landingpage/salespage need a layout

Hi!
We are two people from Sweden looking for help to design our coaching landingpage/salespage.

What about:
We need a nice modern timeless appealing Photoshop layout (landingpage) for our coaching page where we coach people to “how to get a richer lifestyle”.

Style of page:
We want the site to reflect seriousness but still harmonic. We would like somewhat colorful and (but not too crazy). After all, we are coaching about investments and private economy.
Responsive layout – consider stacking order when scaling down window width. Fullpage-design where content areas are 960 grid/max-width.

----------------------------------------------------------------------------
Content on page:
*Headersection – Logo and header image with the two coaches together and space for later on adding a video.

*On the landingpage the customers can read up on what we mean by a richer lifestyle (use dummy text). We show our Vardagskompassen (= Lifestyle matrix) and a little description about that. If the customers want to know more, they can click "read more (or a symbolic icon that relates to read more)" to expand a hidden div (section) where they can read more about Vardagskompassen. They can also minimize the section.

*3-4 Unique selling points “Four reasons why choose coaching” with nice designed number-icons and some place for text.

*The customer should also be able to read something about what happens during a typical coaching session, some bullets that summarize it (use dummy text) and a couple of headlines, maybe 3 or 4 (about what they need to prepare for themselves .eg Skype, headset/microphone etc).

*Offer/product section: A section where the customer can see what services we provide, choose product and click order. When customer click order they will arrive to an order-page (this one you don’t have to design) .
Our products are as followed: Bronze (single coaching session), Silver (small-package), Gold (large-package). Use provided graphics for these products.

*Testimonials section. Currently we have 2 good testimonials, but only with text no portrait picture.

Testimonial1: “Uppiggande och inspirerande! Kommer med enkla vardagstips såväl som svårare tips. Ett roligt sätt att få en spark i baken, så att ekonomi-energin bibehålls! Tack för ett bra samtal!" - Helena Brattvik

Testimonial2: "Värdefullast för mig var kunskapen om alternativa investeringssställen som inte är börs eller eget ägande." - Annika Sjöstedt

*Section with portraits and info about the coaches (currently 2 coaches, but in future will be several, so a design-section that’s lets us add more coaches).

*Footer-section
------------------------------------------------------------------------

Colors:
Use Vardagskompassen (attached file) as colorinspiration. Doesn’t have to be exactly those colors, you can use similar colors if it is more pleasing to the eye and you can also use complementary colors.

Currently we have tried of our own but don't really nail it with any apealing design. This is what we have done so far but we want to replace it with your more professional design:

https://www.harborkite.se/full/Page/coaching13
-------------------------------------------------------------

SUMMARIZE of the above design-description:

* Our logo (attached psd-file with smart-object. You can try different colors with color-overlay)

*Apealing headerimage with portrait (attached file "big_portrait")

*Introduction text (use dummy text about 100 words)

*Text about Vardagskompassen (use dummy text about 200 words)

*Vardagskompassen (attached psd-file with smart-object)

*What we are covering during a coaching session (dummy text about 200 words and about 5 or 6 bullets)

*3-4 Unique Selling Points with stylish number icons (not 2 small) and some text.
*Our offers Bronze, Silver, Gold (attached pictures)
*Testimonials
*Picture & info about coaches (attached pictures, choose whichever suits you)
*Footer

Please comment if there are questions.

Target Market(s)

People who want to learn how to create a richer lifestyle which involves more freedom and a better well-being

Number of Pages Required

1 page

Font styles to use
Sans Serif
Other font styles liked:
• Roboto

Requirements
Should not have
• A cheezy unmodern landingpage with lots of texts and 10 sign-up buttons.
• This page is not a site about capturing emails and building lists by provide a "best-guide-for-something". It´s about getting people to book and pay for one or more coaching-sessions.

```html
<!DOCTYPE html>
<html lang="sv">
<head>
<meta charset="utf-8">
<title>Harbor Kite – Coaching</title>
<link href="https://fonts.googleapis.com/css2?family=Lato:wght@300;400;700;900&family=Open+Sans:wght@400;600;700&display=swap" rel="stylesheet">
<style>
:root{
  --navy:#1d4f7c;
  --navy-dark:#163d61;
  --sky:#29a3dc;
  --ink:#2b2b2b;
  --text:#444;
  --muted:#777;
  --light:#eeeeee;
  --white:#fff;
  --brown:#a47e64;
  --orange:#f59a1d;
  --green:#3cb14a;
  --btn:#333;
  --bar:#111;
}
*{box-sizing:border-box;margin:0;padding:0}
html,body{width:1200px;height:3659px;overflow:hidden}
body{font-family:"Open Sans",Arial,sans-serif;color:var(--text);background:var(--white);position:relative}
.section-title{font-family:"Lato",Arial,sans-serif;font-weight:400;font-size:37px;color:var(--ink);text-align:center;letter-spacing:.5px}
.section-title span{color:var(--sky)}
.title-rule{width:200px;height:12px;margin:8px auto 0;position:relative}
.title-rule:before{content:"";position:absolute;left:0;right:0;top:6px;border-top:1px solid #aaa}
.title-rule:after{content:"";position:absolute;left:96px;top:2px;width:8px;height:8px;background:#777}
.btn-dark{display:inline-block;background:var(--btn);color:#fff;font-family:"Lato",sans-serif;font-weight:700;font-size:14px;padding:6px 22px;border-radius:2px}
.body-copy{font-size:13px;line-height:21px;text-align:center;color:var(--text)}

/* header */
.site-header{height:98px;border-top:4px solid var(--navy);display:flex;align-items:center;justify-content:space-between;padding:0 98px}
.brand{display:flex;align-items:center;gap:14px;font-family:"Lato",sans-serif;font-weight:400;font-size:34px;letter-spacing:2px;color:var(--navy)}
.brand-mark{width:30px;height:30px;background:var(--navy)}
.header-contact{display:flex;gap:22px;font-family:"Lato",sans-serif;font-weight:700;font-size:20px;color:var(--navy);align-items:center}
.header-contact svg{vertical-align:-3px;margin-right:4px}

/* hero */
.hero{position:absolute;top:98px;left:0;width:1200px;height:475px;border-bottom:5px solid var(--navy);
  background:linear-gradient(100deg,#5b4a3a 0%,#b69f82 30%,#e9e2d6 55%,#cfc2ae 80%,#8d7a62 100%)}
.hero-copy{position:absolute;left:100px;top:200px;color:#fff}
.hero-kicker{font-family:"Lato",sans-serif;font-size:28px;font-weight:400}
.hero-title{font-family:"Lato",sans-serif;font-size:37px;font-weight:700;letter-spacing:.5px;margin-top:2px}
.hero-btn{display:inline-flex;align-items:center;gap:10px;margin-top:20px;background:var(--navy);color:#fff;font-family:"Lato",sans-serif;font-weight:700;font-size:15px;padding:7px 10px 7px 14px;border-radius:2px}
.video-frame{position:absolute;left:660px;top:88px;width:440px;height:290px;border:6px solid #f1f1f1;
  background:linear-gradient(180deg,#8fb6e3 0%,#e9b56a 55%,#33312e 100%);box-shadow:0 2px 10px rgba(0,0,0,.35)}
.video-controls{position:absolute;left:0;right:0;bottom:0;height:34px;background:rgba(0,0,0,.75)}

/* about */
.about{position:absolute;top:573px;left:0;width:1200px;height:317px;background:var(--light);padding-top:42px}
.about .body-copy{margin:26px auto 0;width:1000px}
.about .btn-dark{display:block;width:112px;margin:22px auto 0;padding:5px 0;text-align:center;font-size:13px}

/* matrix */
.matrix{position:absolute;top:890px;left:0;width:1200px;height:517px;padding-top:44px}
.matrix .intro{width:1000px;margin:24px auto 0;font-size:13px;line-height:21px;text-align:center;font-weight:600;color:#333}
.pillars{display:flex;justify-content:space-between;width:1000px;margin:30px auto 0}
.pillar{width:220px;text-align:center}
.pillar-icon{width:88px;height:88px;border-radius:50%;margin:0 auto;display:flex;align-items:center;justify-content:center}
.pillar h3{font-family:"Lato",sans-serif;font-size:19px;font-weight:400;margin-top:18px;letter-spacing:.5px}
.pillar p{font-size:13px;line-height:17px;color:#333;margin-top:8px;font-weight:600}
.matrix .btn-dark{display:block;width:118px;margin:36px auto 0;padding:5px 0;text-align:center}

/* why */
.why{position:absolute;top:1407px;left:0;width:1200px;height:647px;background:#f4f4f4;overflow:hidden}
.why-side{position:absolute;left:0;top:0;width:190px;height:100%;background:#e2e2e2;border-right:1px solid #cfcfcf}
.why-art{position:absolute;left:240px;top:60px;width:820px;height:560px;background:radial-gradient(ellipse at center,#e6e9ee 0%,#f4f4f4 70%)}
.why .section-title{position:absolute;top:38px;left:0;width:1200px}
.why .title-rule{position:absolute;top:92px;left:500px;margin:0}
.reason{position:absolute;left:98px;width:1004px;height:90px}
.reason-text{position:absolute;left:100px;top:0;width:870px;height:90px;color:#fff;font-size:11.5px;line-height:21px;padding:12px 0 0 10px}

/* products */
.products{position:absolute;top:2054px;left:0;width:1200px;height:483px}
.products-band{position:absolute;top:0;left:0;width:1200px;height:216px;background:var(--navy)}
.products .section-title{position:absolute;top:34px;width:1200px;color:#fff}
.products .title-rule{position:absolute;top:86px;left:500px;margin:0}
.products .title-rule:before{border-color:#9bb5cf}
.products .title-rule:after{background:#fff}
.product{position:absolute;top:116px;width:260px;text-align:center}
.medal{width:180px;height:180px;border-radius:50%;margin:0 auto;box-shadow:0 6px 12px rgba(0,0,0,.3)}
.product h3{font-family:"Lato",sans-serif;font-size:22px;font-weight:700;color:var(--navy);margin-top:28px;letter-spacing:1px}
.product p{font-size:15px;color:#444;margin-top:2px}
.product .btn-dark{margin-top:10px;width:196px;font-size:15px;padding:7px 0;text-align:center}

/* testimonials */
.testimonials{position:absolute;top:2537px;left:0;width:1200px;height:390px;background:var(--light);padding-top:42px}
.quote-card{position:absolute;top:121px;width:466px;height:148px;background:#fff;padding:20px 24px 0 40px}
.quote-card:after{content:"";position:absolute;left:110px;bottom:-16px;border-width:16px 14px 0 0;border-style:solid;border-color:#fff transparent transparent transparent}
.quote-card blockquote{font-style:italic;font-size:13px;line-height:21px;color:#333}
.quote-mark{position:absolute;left:14px;top:14px}
.quote-author{position:absolute;bottom:14px;left:100px;font-size:13px;color:#333}
.quote-author b{font-weight:700;margin-right:8px;padding-right:8px;border-right:1px solid #999}
.quote-badge{position:absolute;top:284px;width:64px;height:64px;border-radius:50%;background:#cfcfcf;display:flex;align-items:center;justify-content:center}

/* coaches */
.coaches{position:absolute;top:2927px;left:0;width:1200px;height:475px;padding-top:42px}
.coach{position:absolute;top:151px;width:482px;height:275px;border:1px solid #ccc;background:#fff}
.coach-photo{position:absolute;left:0;top:0;width:238px;height:275px;background:var(--navy);padding:10px 10px 0}
.coach-photo .photo{width:218px;height:222px}
.coach-name{color:#fff;font-family:"Lato",sans-serif;font-weight:700;font-size:17px;text-align:center;margin-top:10px}
.coach-bio{position:absolute;left:256px;top:14px;width:210px;font-size:13px;line-height:21px;letter-spacing:.6px;color:#444;text-align:left}

/* footer */
.site-footer{position:absolute;top:3402px;left:0;width:1200px;height:213px;background:var(--navy);color:#fff}
.footer-col{position:absolute;top:36px}
.footer-col h4{font-family:"Lato",sans-serif;font-weight:700;font-size:15px;margin-bottom:12px}
.footer-col li{list-style:none;font-size:12px;margin-bottom:22px}
.footer-col li:before{content:"›";margin-right:10px}
.contact-line{display:flex;gap:10px;font-size:12px;line-height:16px;margin-bottom:16px;align-items:flex-start}
.footer-map{position:absolute;left:561px;top:73px;width:268px;height:110px;background:linear-gradient(135deg,#d9d6cd,#ece9e1)}
.footer-divider{position:absolute;top:24px;height:170px;border-left:1px solid #3e6a93}
.footer-brand{position:absolute;left:930px;top:100px;display:flex;align-items:center;gap:12px;font-family:"Lato",sans-serif;font-size:28px;letter-spacing:2px;color:#fff}
.footer-brand .brand-mark{background:#fff;width:26px;height:26px}
.bottom-bar{position:absolute;top:3615px;left:0;width:1200px;height:44px;background:var(--bar);color:#ccc;font-size:11px;padding:0 98px;display:flex;align-items:center;justify-content:space-between}
.social-dot{width:22px;height:22px;border-radius:50%;border:1px solid #888}
</style>
</head>
<body>

<header class="site-header">
  <div class="brand"><span class="brand-mark"></span>HARBOR KITE</div>
  <div class="header-contact">
    <span><svg width="18" height="18" viewBox="0 0 20 20"><circle cx="10" cy="10" r="8" fill="none" stroke="currentColor" stroke-width="2"/><circle cx="10" cy="10" r="3" fill="none" stroke="currentColor" stroke-width="2"/></svg>team@harborkite.se</span>
    <span><svg width="18" height="18" viewBox="0 0 20 20"><circle cx="10" cy="10" r="9" fill="none" stroke="currentColor" stroke-width="1.6"/><path d="M7 5l2 3-1 1c.6 1.3 1.7 2.4 3 3l1-1 3 2-1 2c-4 0-8-4-8-8z" fill="currentColor"/></svg>123-555-0190</span>
  </div>
</header>

<section class="hero">
  <div role="img" aria-label="Bright mansion interior with sweeping staircase and chandelier" style="position:absolute;inset:0"></div>
  <div class="hero-copy">
    <div class="hero-kicker">Step By Step To</div>
    <div class="hero-title">A RICHER LIFESTYLE</div>
    <span class="hero-btn">WATCH OUR VIDEO
      <svg width="24" height="24" viewBox="0 0 24 24"><circle cx="12" cy="12" r="10.5" fill="none" stroke="#fff" stroke-width="1.6"/><path d="M10 7.5l5 4.5-5 4.5z" fill="#fff"/></svg></span>
  </div>
  <div class="video-frame" role="img" aria-label="Video still of the two coaches standing in a sunny field">
    <div class="video-controls">
      <svg width="428" height="34" viewBox="0 0 428 34"><rect x="26" y="15" width="240" height="4" fill="#666"/><rect x="26" y="15" width="160" height="4" fill="#d33"/><circle cx="186" cy="17" r="6" fill="#fff"/><rect x="300" y="11" width="14" height="12" fill="#ccc"/><rect x="390" y="11" width="16" height="12" fill="none" stroke="#ccc" stroke-width="2"/></svg>
    </div>
  </div>
</section>

<section class="about">
  <h2 class="section-title">ABOUT <span>HARBOR KITE</span></h2>
  <div class="title-rule"></div>
  <p class="body-copy">Lorem ipsum dolor sit amet, consectetuer adipiscing elit, sed diam nonummy nibh euismod tincidunt ut laoreet dolore magna aliquam erat volutpat. Ut wisi enim ad minim veniam, quis nostrud exerci tation ullamcorper suscipit lobortis nisl ut aliquip ex ea commodo consequat. Duis autem vel eum iriure dolor in hendrerit in vulputate velit esse molestie consequat, vel illum dolore eu feugiat nulla facilisis at vero eros et accumsan et iusto odio dignissim qui blandit praesent luptatum zzril delenit augue duis dolore te feugait nulla facilisi.</p>
  <span class="btn-dark">Read More »</span>
</section>

<section class="matrix">
  <h2 class="section-title">OUR <span>LIFESTYLE MATRIX</span></h2>
  <div class="title-rule"></div>
  <p class="intro">What is a richer lifestyle may differ between different people. It can also be quite difficult on their own to get a good picture of what you really mean by this . We have therefore developed a simple model to facilitate the understanding and the creation of a richer lifestyle. This is a model we call lifestyle matrix and consists of the following four parts representing respective lifestyle.</p>
  <div class="pillars">
    <div class="pillar">
      <div class="pillar-icon" style="background:var(--brown)"><svg width="44" height="44" viewBox="0 0 44 44"><path d="M22 20c-4-6-12-3-9 3 2 4 9 8 9 8s7-4 9-8c3-6-5-9-9-3z" fill="#fff"/><path d="M6 34c5-4 10-2 14 0h12l6-4" fill="none" stroke="#fff" stroke-width="3" stroke-linecap="round"/></svg></div>
      <h3 style="color:var(--brown)">PROSPEROUS</h3>
      <p>Lorem ipsum dolor sit am et, consectetuer sit ame Lorem ipsum dolor sit am</p>
    </div>
    <div class="pillar">
      <div class="pillar-icon" style="background:var(--sky)"><svg width="44" height="44" viewBox="0 0 44 44"><circle cx="22" cy="22" r="14" fill="none" stroke="#fff" stroke-width="3"/><path d="M22 22l7-7M14 30h16" stroke="#fff" stroke-width="3" stroke-linecap="round"/></svg></div>
      <h3 style="color:var(--sky)">RAT RACE</h3>
      <p>Lorem ipsum dolor sit am et, consectetuer sit ame Lorem ipsum dolor sit am</p>
    </div>
    <div class="pillar">
      <div class="pillar-icon" style="background:var(--orange)"><svg width="44" height="44" viewBox="0 0 44 44"><circle cx="26" cy="16" r="8" fill="#fff"/><path d="M6 34c5-4 10-2 14 0h12l6-4" fill="none" stroke="#fff" stroke-width="3" stroke-linecap="round"/></svg></div>
      <h3 style="color:var(--orange)">A RICHER</h3>
      <p>Lorem ipsum dolor sit am et, consectetuer sit ame Lorem ipsum dolor sit am</p>
    </div>
    <div class="pillar">
      <div class="pillar-icon" style="background:var(--green)"><svg width="44" height="44" viewBox="0 0 44 44"><path d="M8 24c8-2 12-10 26-14-4 6-6 18-18 20l-4 6-1-6z" fill="#fff"/></svg></div>
      <h3 style="color:var(--green)">FREEDOM</h3>
      <p>Lorem ipsum dolor sit am et, consectetuer sit ame Lorem ipsum dolor sit am</p>
    </div>
  </div>
  <span class="btn-dark">Get Started »</span>
</section>

<section class="why">
  <div class="why-side"></div>
  <div class="why-art" role="img" aria-label="Faint sketch of a growth chart in the background"></div>
  <h2 class="section-title">WHY <span>CHOOSE COACHING ?</span></h2>
  <div class="title-rule"></div>

  <div class="reason" style="top:125px">
    <svg width="1004" height="90" viewBox="0 0 1004 90" style="position:absolute;left:0;top:0"><polygon points="88,0 1004,0 986,45 1004,90 88,90" fill="var(--sky)"/><polygon points="14,0 90,0 90,90 14,90 0,45" fill="var(--sky)" stroke="#fff" stroke-width="2"/><path d="M56 50h6v14h-6zM64 50l6-12c3 0 4 2 3 5l-1 5h8c2 0 3 2 2 4l-3 10c-1 2-2 2-4 2H64z" fill="#fff"/></svg>
    <p class="reason-text">Lorem ipsum dolor sit amet, consectetuer adipiscing elit, sed diam nonummy nibh euismod tincidunt ut laoreet dolore magna aliquam erat volutpat. Ut wisi enim ad minim veniam, quis nostrud exerci tation ullamcorper suscipit lobortis nisl ut aliquip ex ea commodo consequat. Duis autem vel eum iriure dolor in hendrerit in vulputate velit esse molestie consequat, vel illum dolore eu feugiat nulla facilisis at vero.</p>
  </div>
  <div class="reason" style="top:244px">
    <svg width="1004" height="90" viewBox="0 0 1004 90" style="position:absolute;left:0;top:0"><polygon points="88,0 1004,0 986,45 1004,90 88,90" fill="var(--sky)"/><polygon points="14,0 90,0 90,90 14,90 0,45" fill="var(--sky)" stroke="#fff" stroke-width="2"/><path d="M56 50h6v14h-6zM64 50l6-12c3 0 4 2 3 5l-1 5h8c2 0 3 2 2 4l-3 10c-1 2-2 2-4 2H64z" fill="#fff"/></svg>
    <p class="reason-text">Lorem ipsum dolor sit amet, consectetuer adipiscing elit, sed diam nonummy nibh euismod tincidunt ut laoreet dolore magna aliquam erat volutpat. Ut wisi enim ad minim veniam, quis nostrud exerci tation ullamcorper suscipit lobortis nisl ut aliquip ex ea commodo consequat. Duis autem vel eum iriure dolor in hendrerit in vulputate velit esse molestie consequat, vel illum dolore eu feugiat nulla facilisis at vero.</p>
  </div>
  <div class="reason" style="top:364px">
    <svg width="1004" height="90" viewBox="0 0 1004 90" style="position:absolute;left:0;top:0"><polygon points="88,0 1004,0 986,45 1004,90 88,90" fill="var(--sky)"/><polygon points="14,0 90,0 90,90 14,90 0,45" fill="var(--sky)" stroke="#fff" stroke-width="2"/><path d="M56 50h6v14h-6zM64 50l6-12c3 0 4 2 3 5l-1 5h8c2 0 3 2 2 4l-3 10c-1 2-2 2-4 2H64z" fill="#fff"/></svg>
    <p class="reason-text">Lorem ipsum dolor sit amet, consectetuer adipiscing elit, sed diam nonummy nibh euismod tincidunt ut laoreet dolore magna aliquam erat volutpat. Ut wisi enim ad minim veniam, quis nostrud exerci tation ullamcorper suscipit lobortis nisl ut aliquip ex ea commodo consequat. Duis autem vel eum iriure dolor in hendrerit in vulputate velit esse molestie consequat, vel illum dolore eu feugiat nulla facilisis at vero.</p>
  </div>
  <div class="reason" style="top:483px">
    <svg width="1004" height="90" viewBox="0 0 1004 90" style="position:absolute;left:0;top:0"><polygon points="88,0 1004,0 986,45 1004,90 88,90" fill="var(--sky)"/><polygon points="14,0 90,0 90,90 14,90 0,45" fill="var(--sky)" stroke="#fff" stroke-width="2"/><path d="M56 50h6v14h-6zM64 50l6-12c3 0 4 2 3 5l-1 5h8c2 0 3 2 2 4l-3 10c-1 2-2 2-4 2H64z" fill="#fff"/></svg>
    <p class="reason-text">Lorem ipsum dolor sit amet, consectetuer adipiscing elit, sed diam nonummy nibh euismod tincidunt ut laoreet dolore magna aliquam erat volutpat. Ut wisi enim ad minim veniam, quis nostrud exerci tation ullamcorper suscipit lobortis nisl ut aliquip ex ea commodo consequat. Duis autem vel eum iriure dolor in hendrerit in vulputate velit esse molestie consequat, vel illum dolore eu feugiat nulla facilisis at vero.</p>
  </div>
</section>

<section class="products">
  <div class="products-band"></div>
  <h2 class="section-title">OUR PRODUCTS</h2>
  <div class="title-rule"></div>
  <div class="product" style="left:146px">
    <div class="medal" role="img" aria-label="Bronze product medal" style="background:radial-gradient(circle at 40% 35%,#f2a867,#c2672a 60%,#8a4215)"></div>
    <h3>BRONZE</h3><p>single coaching session</p>
    <span class="btn-dark">Make An Appointment</span>
  </div>
  <div class="product" style="left:470px">
    <div class="medal" role="img" aria-label="Gold product medal" style="background:radial-gradient(circle at 40% 35%,#fbe27a,#e2b021 60%,#a97a0c)"></div>
    <h3>GOLD</h3><p>large-package</p>
    <span class="btn-dark">Make An Appointment</span>
  </div>
  <div class="product" style="left:802px">
    <div class="medal" role="img" aria-label="Silver product medal" style="background:radial-gradient(circle at 40% 35%,#f5f5f5,#c4c4c4 60%,#8e8e8e)"></div>
    <h3>SILVER</h3><p>small-package</p>
    <span class="btn-dark">Make An Appointment</span>
  </div>
</section>

<section class="testimonials">
  <h2 class="section-title">CLIENTS <span>TESTIMONIALS</span></h2>
  <div class="title-rule"></div>
  <div class="quote-card" style="left:110px">
    <svg class="quote-mark" width="18" height="30" viewBox="0 0 18 30"><rect x="0" y="0" width="6" height="30" fill="#ccc"/><rect x="10" y="0" width="6" height="30" fill="#ccc"/></svg>
    <blockquote>Uppiggande och inspirerande! Kommer med enkla vardagstips såväl som svårare tips. Ett roligt sätt att få en spark i baken, så att ekonomi-energin bibehålls! Tack för ett bra samtal!</blockquote>
    <div class="quote-author"><b>Helena Brattvik</b>Customer</div>
  </div>
  <div class="quote-badge" style="left:130px"><svg width="26" height="20" viewBox="0 0 26 20"><path d="M0 20V10C0 4 3 1 9 0v4c-3 1-4 3-4 6h5v10zM14 20V10c0-6 3-9 9-10v4c-3 1-4 3-4 6h5v10z" fill="#555"/></svg></div>

  <div class="quote-card" style="left:636px">
    <svg class="quote-mark" width="18" height="30" viewBox="0 0 18 30"><rect x="0" y="0" width="6" height="30" fill="#ccc"/><rect x="10" y="0" width="6" height="30" fill="#ccc"/></svg>
    <blockquote>Värdefullast för mig var kunskapen om alternativa investeringssställen som inte är börs eller eget ägande.</blockquote>
    <div class="quote-author"><b>Annika Sjöstedt</b>Customer</div>
  </div>
  <div class="quote-badge" style="left:656px"><svg width="26" height="20" viewBox="0 0 26 20"><path d="M0 20V10C0 4 3 1 9 0v4c-3 1-4 3-4 6h5v10zM14 20V10c0-6 3-9 9-10v4c-3 1-4 3-4 6h5v10z" fill="#555"/></svg></div>
</section>

<section class="coaches">
  <h2 class="section-title">OUR <span>COACHES</span></h2>
  <div class="title-rule"></div>
  <article class="coach" style="left:98px">
    <div class="coach-photo"><div class="photo" role="img" aria-label="Portrait of coach Joakim Falkner" style="background:linear-gradient(160deg,#b9c2cc,#5a6470)"></div><div class="coach-name">Joakim Falkner</div></div>
    <p class="coach-bio">Joakim har lång erfarenhet av privatekonomi och budget. Som investerare fokuserar han på fonder, sparande och långsiktiga mål. Han brinner för att göra ekonomi enkel och vill hjälpa fler människor…[+]</p>
  </article>
  <article class="coach" style="left:620px">
    <div class="coach-photo"><div class="photo" role="img" aria-label="Portrait of coach Henrik Lindahl" style="background:linear-gradient(160deg,#9fb7cf,#4f6e4f)"></div><div class="coach-name">Henrik Lindahl</div></div>
    <p class="coach-bio">Henrik är en nyfiken investerare med intresse för hållbara bolag och smarta sparformer. Han har arbetat med rådgivning i många år och hittar gärna nya vägar till frihet i vardagen…[+]</p>
  </article>
</section>

<footer class="site-footer">
  <div class="footer-col" style="left:98px">
    <h4>Quick Links</h4>
    <ul><li>Blog</li><li>Coaching</li><li>About Us</li></ul>
  </div>
  <div class="footer-divider" style="left:248px"></div>
  <div class="footer-col" style="left:273px">
    <h4>Contact Detail</h4>
    <div class="contact-line"><svg width="14" height="18" viewBox="0 0 14 18"><path d="M7 0a7 7 0 0 0-7 7c0 5 7 11 7 11s7-6 7-11a7 7 0 0 0-7-7zm0 10a3 3 0 1 1 0-6 3 3 0 0 1 0 6z" fill="#fff"/></svg><span><b>Harbor Kite</b><br>AB Solviksgatan 12 411 05 Göteborg</span></div>
    <div class="contact-line"><svg width="14" height="14" viewBox="0 0 20 20"><path d="M5 2l3 4-2 2c1 3 3 5 6 6l2-2 4 3-2 3C8 18 2 12 2 4z" fill="#fff"/></svg>(0123) 555-0142</div>
    <div class="contact-line"><svg width="14" height="12" viewBox="0 0 14 12"><rect x="0" y="0" width="14" height="12" fill="#fff"/><path d="M0 0l7 6 7-6" fill="none" stroke="#1d4f7c" stroke-width="1.5"/></svg>team@harborkite.se</div>
  </div>
  <div class="footer-divider" style="left:536px"></div>
  <div class="footer-col" style="left:561px"><h4>Map</h4></div>
  <div class="footer-map" role="img" aria-label="Street map showing the office location"></div>
  <div class="footer-divider" style="left:856px"></div>
  <div class="footer-brand"><span class="brand-mark"></span>HARBOR KITE</div>
</footer>
<div class="bottom-bar"><span>© 2016 Harbor Kite.All Rights Reserved</span><span class="social-dot"></span></div>

</body>
</html>
```